Walk Beside The River

Business Card design

Target Market(s)

People who require support in the commnity

Industry/Entity Type

Mental Health Support

Contact Information for Business Card

Mental Health Support Rosalind Tavener walkbesidetheriver@mailcove.com.au 0481 637 092 PO Box 926 Maroochydore QLD 4558

Colors
6B429C
8869AF
B7A5CE
E3DAEB
F3F0F8

Requirements
Must have
• Logo & details listed above
Should not have
• No red or orange

```html
<!DOCTYPE html>
<html lang="en">
<head>
<meta charset="utf-8">
<title>Walk Beside The River – Business Card</title>
<link href="https://fonts.googleapis.com/css2?family=Open+Sans:wght@400;700&display=swap" rel="stylesheet">
<style>
  :root {
    --page: #2b2b2e;
    --card: #1f1e23;
    --purple: #6b429c;
    --yellow: #e8e22b;
    --olive: #3c3c2e;
    --text: #f3f0f8;
  }
  * { margin: 0; padding: 0; box-sizing: border-box; }
  html, body { width: 1200px; height: 780px; overflow: hidden; }
  body {
    background: var(--page);
    font-family: "Open Sans", Arial, sans-serif;
    color: var(--text);
    display: flex;
    align-items: center;
    justify-content: center;
    gap: 60px;
  }
  .card {
    position: relative;
    width: 520px;
    height: 298px;
    background: var(--card);
    overflow: hidden;
  }
  /* Brand lockup: plain circle + name in one weight */
  .brand {
    display: flex;
    align-items: center;
    gap: 14px;
  }
  .brand-dot {
    border-radius: 50%;
    background: var(--purple);
    flex: none;
  }
  .brand-name {
    font-weight: 400;
    color: var(--text);
    letter-spacing: 0.04em;
    white-space: nowrap;
  }

  /* Details side */
  .card-details .brand { position: absolute; left: 34px; top: 24px; }
  .card-details .brand-dot { width: 70px; height: 70px; }
  .card-details .brand-name { font-size: 15px; }
  .glow {
    position: absolute;
    right: -140px;
    bottom: -170px;
    width: 330px;
    height: 330px;
    border-radius: 50%;
    background: var(--olive);
  }
  .details {
    position: absolute;
    left: 34px;
    top: 112px;
    list-style: none;
    font-size: 12.5px;
    line-height: 19px;
  }
  .details li { display: flex; align-items: center; gap: 8px; white-space: nowrap; }
  .details .plain { padding-left: 22px; }
  .icon { width: 14px; height: 14px; flex: none; }
  .icon path, .icon rect, .icon circle { fill: none; stroke: var(--yellow); stroke-width: 1.8; stroke-linecap: round; stroke-linejoin: round; }
  .person {
    position: absolute;
    right: 42px;
    bottom: 18px;
    text-align: right;
    white-space: nowrap;
  }
  .person-name {
    font-weight: 700;
    font-size: 22px;
    color: var(--yellow);
    line-height: 1.15;
  }
  .person-role { font-size: 13px; color: var(--text); line-height: 1.3; }
  .edge-bar {
    position: absolute;
    right: 0;
    bottom: 18px;
    width: 16px;
    height: 48px;
    background: var(--yellow);
  }

  /* Logo side */
  .card-logo { display: flex; align-items: center; justify-content: center; }
  .card-logo .brand-dot { width: 120px; height: 120px; }
  .card-logo .brand-name { font-size: 22px; }
</style>
</head>
<body>
  <section class="card card-details">
    <div class="glow" role="img" aria-label="Faint brand decoration in muted olive"></div>
    <div class="brand">
      <span class="brand-dot"></span>
      <span class="brand-name">Walk Beside The River</span>
    </div>
    <ul class="details">
      <li class="plain">Mental Health Support</li>
      <li class="plain">Rosalind Tavener</li>
      <li>
        <svg class="icon" viewBox="0 0 16 16" aria-hidden="true"><path d="M4 2l2.5 3-1.5 1.5c.8 1.8 2.2 3.2 4 4l1.5-1.5 3 2.5-1.5 2.5C6 13.5 2.5 10 1.5 3.5z"/></svg>
        <span>0481 637 092</span>
      </li>
      <li>
        <svg class="icon" viewBox="0 0 16 16" aria-hidden="true"><rect x="1.5" y="3.5" width="13" height="9" rx="1"/><path d="M1.5 4l6.5 5 6.5-5"/></svg>
        <span>walkbesidetheriver@mailcove.com.au</span>
      </li>
      <li>
        <svg class="icon" viewBox="0 0 16 16" aria-hidden="true"><path d="M8 15s5-5 5-9a5 5 0 0 0-10 0c0 4 5 9 5 9z"/><circle cx="8" cy="6" r="1.8"/></svg>
        <span>PO Box 926 Coral Reach QLD 4572</span>
      </li>
    </ul>
    <div class="person">
      <p class="person-name">Ilona Marchetti</p>
      <p class="person-role">CEO/Director</p>
    </div>
    <span class="edge-bar"></span>
  </section>

  <section class="card card-logo">
    <div class="brand">
      <span class="brand-dot"></span>
      <span class="brand-name">Walk Beside The River</span>
    </div>
  </section>
</body>
</html>
```